Home Security Company Business Card

Looking for a eye catching business card that is non traditional and stands out but yet still looks professional. It should include all the pertinent information such as name, title, address, telephone, e-mail, website address should definitely stand out and then finally the logo.

Target Market(s)

Residential and Commercial accounts mostly upscale accounts

Industry/Entity Type

Security

Contact Information for Business Card

Name
Title
Address
Office #
Cell #
E-mail
Website

Font styles to use
Serif
Sans Serif

Requirements
Must have
• Logo, two sided color configuration
Nice to have
• You decide
Should not have
• There really aren't any.

```html
<!DOCTYPE html>
<html lang="en">
<head>
<meta charset="utf-8">
<title>Wardlow Security Systems – Business Card</title>
<link href="https://fonts.googleapis.com/css2?family=Cinzel:wght@700&family=Open+Sans:wght@400;600;700&display=swap" rel="stylesheet">
<style>
  :root{
    --bg:#e9e6e1;
    --white:#ffffff;
    --red:#a8161c;
    --red-deep:#7e0f14;
    --gold:#e0bf55;
    --gold-light:#f6ecc4;
    --gold-dark:#c9a53c;
    --ink-light:#ffffff;
  }
  *{margin:0;padding:0;box-sizing:border-box}
  html,body{width:1200px;height:780px;overflow:hidden;background:var(--bg)}
  .canvas{position:relative;width:1200px;height:780px}
  .card{position:absolute;width:540px;height:308px;overflow:hidden;
        box-shadow:0 6px 18px rgba(0,0,0,.18)}
  .card--front{left:40px;top:236px;background:var(--white)}
  .card--back{left:620px;top:236px;
        background:radial-gradient(ellipse at 50% 50%,var(--gold-light) 0%,#e9d28a 45%,var(--gold-dark) 100%)}
  .card__waves{position:absolute;inset:0}

  .brand{position:absolute;font-family:'Cinzel',serif;font-weight:700;color:var(--red);
         text-transform:uppercase;line-height:1}
  .brand__mark{position:absolute;width:34px;height:34px;border-radius:50%;background:var(--gold)}
  .card--front .brand__mark{left:26px;top:86px}
  .card--front .brand{left:74px;top:60px}
  .brand__name{display:block;font-size:46px;letter-spacing:1px}
  .brand__sub{display:block;font-size:15.5px;letter-spacing:.5px;margin-top:4px}
  .card--back .brand{left:0;right:0;top:108px;text-align:center}
  .card--back .brand__name{font-size:60px}
  .card--back .brand__sub{font-size:20px;margin-top:6px}

  .address{position:absolute;right:22px;top:124px;text-align:right;
           font-family:'Open Sans',sans-serif;font-size:12px;line-height:1.45;color:var(--ink-light)}

  .contact{position:absolute;left:28px;top:196px;font-family:'Open Sans',sans-serif;color:var(--ink-light)}
  .contact__name{font-size:17px;font-weight:700;line-height:1.15}
  .contact__title{font-size:11.5px;margin-bottom:6px}
  .contact__row{display:flex;align-items:center;gap:7px;font-size:11.5px;line-height:1.5}
  .icon{width:13px;height:13px;flex:none}
</style>
</head>
<body>
<div class="canvas">

  <section class="card card--front" aria-label="Business card front">
    <svg class="card__waves" viewBox="0 0 540 308" aria-hidden="true">
      <path d="M418 0 C370 106 292 152 172 166 C96 175 36 180 0 184 L0 308 L540 308 L540 0 Z" fill="var(--gold)"/>
      <path d="M432 0 C384 114 304 164 184 178 C104 187 40 191 0 196 L0 308 L540 308 L540 0 Z" fill="var(--red)"/>
    </svg>

    <span class="brand__mark"></span>
    <div class="brand">
      <span class="brand__name">Wardlow</span>
      <span class="brand__sub">Security Systems Inc.</span>
    </div>

    <p class="address">your address Rd.,<br>Suite 000, Larkmoor, USA</p>

    <div class="contact">
      <p class="contact__name">Employee Name</p>
      <p class="contact__title">Managing Director</p>
      <p class="contact__row">
        <svg class="icon" viewBox="0 0 14 14" aria-label="Office phone"><rect width="14" height="14" rx="2" fill="#fff"/><path d="M4 3.2h1.6l.8 2-1 .8a5 5 0 0 0 2.6 2.6l.8-1 2 .8V10c0 .5-.4.9-.9.9A6.9 6.9 0 0 1 3.1 4.1c0-.5.4-.9.9-.9z" fill="var(--red)"/></svg>
        555-014-2290
      </p>
      <p class="contact__row">
        <svg class="icon" viewBox="0 0 14 14" aria-label="Mobile phone"><rect width="14" height="14" rx="2" fill="#fff"/><rect x="4.5" y="2.5" width="5" height="9" rx="1" fill="var(--red)"/><rect x="5.5" y="3.6" width="3" height="5.6" fill="#fff"/></svg>
        +1 555-014-2291
      </p>
      <p class="contact__row">
        <svg class="icon" viewBox="0 0 14 14" aria-label="Email"><rect width="14" height="14" rx="2" fill="#fff"/><rect x="2.5" y="4" width="9" height="6.5" fill="var(--red)"/><path d="M2.5 4l4.5 3.6L11.5 4" stroke="#fff" stroke-width="1" fill="none"/></svg>
        info@wardlowsecure.com
      </p>
    </div>
  </section>

  <section class="card card--back" aria-label="Business card back">
    <div class="brand">
      <span class="brand__name">Wardlow</span>
      <span class="brand__sub">Security Systems Inc.</span>
    </div>
  </section>

</div>
</body>
</html>
```